Animal Eye Clinic needs a Business card

We are a new veterinary ophthalmology practice (Ridgeline Pet Vision Care) and we need a business card designed. We only see animal eyes - we are not a regular veterinary clinic. We already have a logo. We are looking for a professional, good looking business card to hand out to our clients. We are looking for something simple but professional and contemporary. Our logo is likely the only picture/graphic that needs to be on the card.
Updates

Contact Information for Business Card

Delia Vossman, BSc, DVM, MSc, DipACVO
Veterinary Ophthalmologist

Phone: 250.418.3927
Email: ridgelinepetvisioncare@mailbox-example.net
Website: ridgelinepetvisioncare-example.net
Address: 1874 Thornbury Rd
Kelowna, BC, V1X 4M9

Colors

Designer to choose colors to be used in the design.

Requirements
Must have
• Our logo (attached)

```html
<!DOCTYPE html>
<html lang="en">
<head>
<meta charset="utf-8">
<title>Ridgeline Pet Vision Care – Business Card</title>
<link rel="stylesheet" href="https://fonts.googleapis.com/css2?family=Arimo:wght@400;700&display=swap">
<style>
  :root {
    --teal: #0b98aa;
    --teal-deep: #08889a;
    --paper: #f5f5f5;
    --ink: #5a5a5a;
    --white: #ffffff;
    --backdrop: #e4e4e2;
  }
  * { box-sizing: border-box; margin: 0; padding: 0; }
  html, body {
    width: 1200px; height: 864px; overflow: hidden;
    background: var(--backdrop);
    font-family: "Arimo", Arial, sans-serif;
  }
  .sheet {
    width: 1200px; height: 864px;
    display: flex; align-items: center; justify-content: center; gap: 40px;
  }
  .card {
    width: 540px; height: 309px;
    position: relative; overflow: hidden;
    box-shadow: 0 6px 18px rgba(0,0,0,0.18);
  }

  /* Front */
  .card-front {
    background: radial-gradient(circle at 62% 40%, var(--teal) 0%, var(--teal-deep) 100%);
    color: var(--white);
  }
  .front-brand {
    position: absolute; left: 44px; top: 86px;
    display: flex; align-items: center; gap: 18px;
  }
  .brand-dot {
    width: 64px; height: 64px; border-radius: 50%;
    background: var(--white);
    flex: none;
  }
  .brand-name {
    font-weight: 700; text-transform: uppercase;
    letter-spacing: 0.04em; line-height: 1.1;
    color: var(--white);
  }
  .front-brand .brand-name { font-size: 30px; }
  .front-web {
    position: absolute; left: 44px; bottom: 46px;
    font-weight: 700; font-size: 19px; color: var(--white);
  }

  /* Back */
  .card-back { background: var(--paper); color: var(--ink); }
  .back-band {
    position: absolute; left: 0; top: 0; right: 0; height: 106px;
    background: var(--teal);
    display: flex; align-items: center; padding-left: 30px; gap: 12px;
  }
  .back-band .brand-dot { width: 36px; height: 36px; }
  .back-band .brand-name { font-size: 18px; }
  .person {
    position: absolute; right: 30px; top: 126px; text-align: left;
    width: 250px;
  }
  .person-name {
    font-size: 22px; text-transform: uppercase; letter-spacing: 0.02em;
    color: var(--ink);
  }
  .person-creds, .person-title {
    font-size: 13px; color: var(--teal); line-height: 1.3;
  }
  .contact {
    position: absolute; left: 30px; top: 196px;
    list-style: none; font-size: 12.5px; line-height: 1.55;
  }
  .contact .label { font-weight: 700; color: var(--teal); margin-right: 4px; }
  .address {
    position: absolute; left: 30px; bottom: 20px;
    font-size: 14.5px; color: var(--ink);
  }
</style>
</head>
<body>
<main class="sheet">
  <section class="card card-front" aria-label="Card front">
    <div class="front-brand">
      <span class="brand-dot" aria-hidden="true"></span>
      <span class="brand-name">Ridgeline<br>Pet Vision Care</span>
    </div>
    <p class="front-web">ridgelinepetvisioncare-example.net</p>
  </section>

  <section class="card card-back" aria-label="Card back">
    <header class="back-band">
      <span class="brand-dot" aria-hidden="true"></span>
      <span class="brand-name">Ridgeline Pet Vision Care</span>
    </header>
    <div class="person">
      <h1 class="person-name">Delia Vossman</h1>
      <p class="person-creds">BSc, DVM, MSc, DipACVO</p>
      <p class="person-title">Veterinary Ophthalmologist</p>
    </div>
    <ul class="contact">
      <li><span class="label">p:</span>250 418 3927</li>
      <li><span class="label">m:</span>ridgelinepetvisioncare@mailbox-example.net</li>
      <li><span class="label">w:</span>ridgelinepetvisioncare-example.net</li>
    </ul>
    <p class="address">1874 Thornbury Rd, Kelowna, BC, V1X 4M9</p>
  </section>
</main>
</body>
</html>
```